UI/ UX Design for ERP Software

We need a new UX/UI interface for a ERP software for property managers. Our CMMS / ERP solution is made based on responsive design technologies and is coded in PHP.
The overall UX to be similar to Tev Ulna - easy navigation, intuitive menus.

Industry/Entity Type

Property Management

Number of Pages Required

5+ page

Requirements
Must have
• Round dock buttons
Consistent icons across the application
Enough Spacing between buttons/icons/ menu
Consistent Font
Nice to have
• We would like the UX to allow the users to use the application without /minimum training.
Should not have
• we don't want anything that is classic with respect to UX

```html
<!DOCTYPE html>
<html lang="en">
<head>
<meta charset="utf-8">
<title>Estora – Active Dashboard</title>
<link href="https://fonts.googleapis.com/css2?family=Roboto:wght@400;500;700&display=swap" rel="stylesheet">
<style>
  :root{
    --page:#ffffff;
    --shell:#f7f7f7;
    --panel:#ffffff;
    --line:#e6e6e6;
    --text:#4a4a4a;
    --muted:#8a8a8a;
    --brand:#1a8cff;
    --card-a:#00c0ff;
    --card-b:#0a7dff;
    --bar:#0a7dff;
    --alert:#ff3b3b;
    --online:#2ecc40;
  }
  *{box-sizing:border-box;margin:0;padding:0}
  html,body{width:1069px;height:1200px;overflow:hidden;background:var(--page);font-family:"Roboto",sans-serif;color:var(--text)}
  .dashboard{position:absolute;left:34px;top:305px;width:1000px;height:590px;background:var(--panel);box-shadow:0 6px 30px rgba(0,0,0,.12)}
  .topbar{height:72px;background:var(--shell);display:flex;align-items:center;position:relative}
  .brand-block{height:72px;width:205px;background:var(--panel);border-radius:0 36px 36px 0;display:flex;align-items:center;padding-left:18px;gap:18px}
  .menu-toggle{width:12px;display:flex;flex-direction:column;gap:2px}
  .menu-toggle span{height:2px;background:#555}
  .brand-name{display:flex;align-items:center;gap:8px;font-size:26px;font-weight:700;color:var(--brand)}
  .brand-name i{width:22px;height:22px;background:var(--brand);display:block}
  .crumb{margin-left:22px;font-size:12px;color:var(--muted);line-height:16px}
  .crumb svg{display:block;margin-bottom:2px}
  .search{position:absolute;left:366px;top:20px;width:352px;height:32px;background:var(--panel);border:1px solid var(--line);display:flex;align-items:center;justify-content:space-between;padding:0 12px;font-size:12px;color:var(--muted)}
  .tools{position:absolute;left:763px;top:27px;display:flex;gap:14px}
  .tool{position:relative;width:14px;height:14px}
  .tool b{position:absolute;right:-3px;top:-4px;width:6px;height:6px;border-radius:50%;background:var(--alert)}
  .user{position:absolute;left:858px;top:17px;display:flex;align-items:center;gap:12px;font-size:12px}
  .avatar{position:relative;width:36px;height:36px;border-radius:50%;background:radial-gradient(circle at 50% 45%,#c89478,#6a4a3a)}
  .avatar::after{content:"";position:absolute;right:0;bottom:0;width:9px;height:9px;border-radius:50%;background:var(--online);border:2px solid var(--shell)}
  .stats{display:flex;gap:7px;padding:8px 9px 0}
  .stat{flex:1;height:145px;border-radius:3px;background:linear-gradient(135deg,var(--card-a),var(--card-b));color:#fff;padding:26px 13px 0}
  .stat svg{display:block}
  .stat .value{font-size:20px;font-weight:500;margin-top:8px}
  .stat .value small{font-size:7px;font-weight:400}
  .stat .label{font-size:12px;margin-top:30px}
  .activity{margin:8px 9px 0;height:306px;border:1px solid var(--line);position:relative}
  .ranges{position:absolute;left:0;top:0;width:776px;height:28px;background:var(--shell);display:flex;align-items:center;justify-content:flex-end;padding-right:12px;font-size:9px;color:var(--muted);gap:6px}
  .ranges .on{color:var(--brand)}
  .period{position:absolute;left:9px;top:38px;font-size:11px;display:flex;align-items:center;gap:6px}
  .chart{position:absolute;left:6px;top:64px}
  .legend{position:absolute;left:790px;top:70px;list-style:none;font-size:9.5px}
  .legend li{display:flex;align-items:center;gap:10px;height:20px}
  .legend i{width:8px;height:8px;display:block}
  .scroll{position:absolute;left:119px;bottom:3px;width:572px;height:2px;background:#ddd}
</style>
</head>
<body>
<main class="dashboard">
  <header class="topbar">
    <div class="brand-block">
      <div class="menu-toggle"><span></span><span></span><span></span></div>
      <div class="brand-name"><i></i>Estora</div>
    </div>
    <div class="crumb">
      <svg width="10" height="9" viewBox="0 0 10 9"><path d="M5 0 0 4.5h1.5V9h2.5V6h2v3h2.5V4.5H10z" fill="#999"/></svg>
      Active Dashboard
    </div>
    <div class="search">Search
      <svg width="12" height="12" viewBox="0 0 12 12"><circle cx="5" cy="5" r="3.8" fill="none" stroke="#777" stroke-width="1.4"/><path d="M8 8l3 3" stroke="#777" stroke-width="1.4"/></svg>
    </div>
    <div class="tools">
      <div class="tool"><svg width="14" height="14" viewBox="0 0 14 14"><path d="M7 1a4 4 0 0 0-4 4v4L1.5 11h11L11 9V5a4 4 0 0 0-4-4zM5.5 12a1.5 1.5 0 0 0 3 0z" fill="#888"/></svg><b></b></div>
      <div class="tool"><svg width="14" height="14" viewBox="0 0 14 14"><rect x="1" y="3" width="12" height="9" fill="none" stroke="#888" stroke-width="1.3"/><path d="M1 3l6 5 6-5" fill="none" stroke="#888" stroke-width="1.3"/></svg><b></b></div>
      <div class="tool"><svg width="14" height="14" viewBox="0 0 14 14" fill="#888"><rect x="1" y="2" width="3" height="2.5"/><rect x="5" y="2" width="8" height="2.5"/><rect x="1" y="6" width="3" height="2.5"/><rect x="5" y="6" width="8" height="2.5"/><rect x="1" y="10" width="3" height="2.5"/><rect x="5" y="10" width="8" height="2.5"/></svg></div>
    </div>
    <div class="user">
      <div class="avatar" role="img" aria-label="User profile photo"></div>
      <span>Lorawen &#8964;</span>
    </div>
  </header>

  <section class="stats">
    <article class="stat">
      <svg width="14" height="12" viewBox="0 0 10 9"><path d="M5 0 0 4.5h1.5V9h2.5V6h2v3h2.5V4.5H10z" fill="#fff"/></svg>
      <div class="value">3</div><div class="label">Properties</div>
    </article>
    <article class="stat">
      <svg width="18" height="13" viewBox="0 0 18 13" fill="#fff"><circle cx="4" cy="3" r="2.3"/><circle cx="9" cy="2.8" r="2.6"/><circle cx="14" cy="3" r="2.3"/><path d="M0 11c0-3 2-4.5 4-4.5S8 8 8 11zM5 12.5c0-3.5 2-5 4-5s4 1.5 4 5zM10 11c0-3 2-4.5 4-4.5s4 1.5 4 4.5z"/></svg>
      <div class="value">8</div><div class="label">Tenants</div>
    </article>
    <article class="stat">
      <svg width="14" height="14" viewBox="0 0 14 14" fill="#fff"><path d="M0 0h5L3.5 1.5 6 4 4 6 1.5 3.5 0 5zM14 0v5l-1.5-1.5L10 6 8 4l2.5-2.5L9 0zM0 14V9l1.5 1.5L4 8l2 2-2.5 2.5L5 14zM14 14H9l1.5-1.5L8 10l2-2 2.5 2.5L14 9z"/></svg>
      <div class="value">422,000.00<small>Sq.Ft</small></div><div class="label">Total Properties Area</div>
    </article>
    <article class="stat">
      <svg width="14" height="14" viewBox="0 0 14 14" fill="#fff"><path d="M0 0h5L3.5 1.5 6 4 4 6 1.5 3.5 0 5zM14 0v5l-1.5-1.5L10 6 8 4l2.5-2.5L9 0zM0 14V9l1.5 1.5L4 8l2 2-2.5 2.5L5 14zM14 14H9l1.5-1.5L8 10l2-2 2.5 2.5L14 9z"/></svg>
      <div class="value">233,500.00<small>Sq.Ft</small></div><div class="label">Rented Area</div>
    </article>
    <article class="stat">
      <svg width="14" height="14" viewBox="0 0 14 14" fill="#fff"><path d="M0 0h5L3.5 1.5 6 4 4 6 1.5 3.5 0 5zM14 0v5l-1.5-1.5L10 6 8 4l2.5-2.5L9 0zM0 14V9l1.5 1.5L4 8l2 2-2.5 2.5L5 14zM14 14H9l1.5-1.5L8 10l2-2 2.5 2.5L14 9z"/></svg>
      <div class="value">188,500.00<small>Sq.Ft</small></div><div class="label">Vacancies Area</div>
    </article>
  </section>

  <section class="activity">
    <nav class="ranges">
      <span class="on">&#9719; Last 7 days</span>|<span>&#9719; Last Months</span>|<span>&#9719; Last 3 Months</span>|<span>&#9719; Next 7 days</span>|<span>&#9719; Next Months</span>|<span>&#9719; Next 3 Months</span>
    </nav>
    <div class="period">
      <svg width="12" height="9" viewBox="0 0 12 9" fill="var(--brand)"><rect x="0" y="7" width="2" height="2"/><rect x="3" y="5" width="2" height="4"/><rect x="6" y="3" width="2" height="6"/><rect x="9" y="0" width="2" height="9"/></svg>
      12/27/2020 - 01/03/2021
    </div>
    <svg class="chart" width="770" height="200" viewBox="0 0 770 200" font-family="Roboto, sans-serif" font-size="9" fill="#888">
      <g stroke="#ececec">
        <line x1="24" y1="6" x2="760" y2="6"/><line x1="24" y1="38.5" x2="760" y2="38.5"/>
        <line x1="24" y1="71" x2="760" y2="71"/><line x1="24" y1="103.5" x2="760" y2="103.5"/>
        <line x1="24" y1="136" x2="760" y2="136"/><line x1="24" y1="168.5" x2="760" y2="168.5"/>
      </g>
      <g>
        <text x="3" y="9">1.25</text><text x="3" y="41.5">1</text><text x="3" y="74">0.75</text>
        <text x="3" y="106.5">0.5</text><text x="3" y="139">0.25</text><text x="3" y="171.5">0</text>
      </g>
      <g stroke="#ccc">
        <line x1="98" y1="168.5" x2="98" y2="178"/><line x1="195" y1="168.5" x2="195" y2="178"/>
        <line x1="292" y1="168.5" x2="292" y2="178"/><line x1="389" y1="168.5" x2="389" y2="178"/>
        <line x1="486" y1="168.5" x2="486" y2="178"/><line x1="583" y1="168.5" x2="583" y2="178"/>
        <line x1="680" y1="168.5" x2="680" y2="178"/>
      </g>
      <g>
        <text x="24" y="190">12/27/2020</text><text x="121" y="190">12/28/2020</text>
        <text x="218" y="190">12/29/2020</text><text x="315" y="190">12/30/2020</text>
        <text x="412" y="190">12/31/2020</text><text x="508" y="190">01/01/2021</text>
        <text x="605" y="190">01/02/2021</text><text x="715" y="190">01/03/2021</text>
      </g>
      <rect x="302" y="38.5" width="4" height="130" fill="var(--bar)"/>
    </svg>
    <ul class="legend">
      <li><i style="background:#a9cbea"></i>Scheduled Maintenance</li>
      <li><i style="background:#8ee06b"></i>Completed Scheduled Maintenance</li>
      <li><i style="background:#f4a04a"></i>Future Scheduled Maintenance</li>
      <li><i style="background:#3a3a3a"></i>Scheduled Work Orders</li>
      <li><i style="background:#7f7fe0"></i>Completed Work Orders</li>
      <li><i style="background:#f2557a"></i>Property Inspections in Progress</li>
      <li><i style="background:#e8d24a"></i>Completed Property Inspections</li>
    </ul>
    <div class="scroll"></div>
  </section>
</main>
</body>
</html>
```